New Organic Skin Care Line Needs to Design a Product Label

***THE WINNER OF THIS PROJECT WILL MOST LIKELY BECOME THE EXCLUSIVE DESIGNER FOR OUR OTHER PRODUCT LABELS***

We need a label design for a new organic skin care product line called "Maple Dew Gala." This specific product is a 100% pure organic coconut oil. It's used for skin hydration, protection, and makeup removal.

Info to include on front label:

1. Logo: Maple Dew Gala (attached)
2. Product Name: Pure Coconut Oil (emphasize "organic" somewhere)
3. Slogan: Hydrate your skin and hair.
4. Size: 8 FL OZ 236mL

Attached is:

1. The brand logo "Maple Dew Gala" with a white background.
2. An image of the bottle we will use.
3. An image of the bottle with lines to show the size and placement of the label.
4. The brand logo "Maple Dew Gala" with a black background. (photoshop file)

What we need:

A simple mock up of the front side of the label on the bottle. We first want to know what it will look like on the bottle given the size and dimensions.

- We would like one label with a white background (including the logo with a white background).
- We would like a second label with a black background (including the logo with a black background, just need to make the black font white instead of black).

We can get a great idea of what to expect from the front side of the label so we will complete the back side once we identify a winner.
Updates

Apologies, but we are now using a different bottle. The previous one is now discontinued. Please view the two most recent images uploaded. One is an image of the new bottle by itself. The other is an image of that bottle with instructions. Please use your most recent designs on the new bottle. Feel free to make any modifications you see fit to compliment the new bottle shape. Added Friday, March 18, 2016

Reason: We are still working with the label company to finalize the size. Once the size is confirmed we will have to tweak labels based on finalized measurements.

Target Market(s)

Women, 18-70

Industry/Entity Type

Skin Care Product

Font styles to use
Decorative
Script

Requirements
Must have
• -"shabby sheek" and "cute" theme
• -soft organic feel
• -the ingredients are organic, pure, and natural. That should be an essence of the label.

```html
<!DOCTYPE html>
<html lang="en">
<head>
<meta charset="utf-8">
<title>Maple Dew Gala – Pure Coconut Oil Label</title>
<link rel="stylesheet" href="https://fonts.googleapis.com/css2?family=Cinzel:wght@400&family=Libre+Baskerville:wght@400;700&family=Comfortaa:wght@400&family=Arimo:wght@400&display=swap">
<style>
  :root {
    --page: #ffffff;
    --label: #000000;
    --ink: #ffffff;
    --organic: #9bc53d;
    --coconut-shell: #8a6a4a;
    --coconut-flesh: #f2efe8;
  }
  html, body {
    margin: 0;
    padding: 0;
    overflow: hidden;
    background: var(--page);
  }
  .canvas {
    position: relative;
    width: 716px;
    height: 1200px;
    background: var(--page);
    overflow: hidden;
  }
  .label-shape {
    position: absolute;
    inset: 0;
  }
  .label-copy {
    position: absolute;
    left: 223px;
    top: 0;
    width: 360px;
    height: 1200px;
  }
  .label-text {
    position: absolute;
    left: 0;
    width: 100%;
    margin: 0;
    text-align: center;
    color: var(--ink);
    line-height: 1;
    white-space: nowrap;
  }
  .brand-name {
    top: 814px;
    font-family: "Cinzel", serif;
    font-size: 17px;
    letter-spacing: 3px;
  }
  .product-art {
    position: absolute;
    left: 115px;
    top: 852px;
    width: 130px;
    height: 52px;
    border-radius: 26px;
    background: radial-gradient(ellipse at 45% 55%, var(--coconut-flesh) 0%, #cdbb9f 45%, var(--coconut-shell) 75%, rgba(0,0,0,0) 100%);
  }
  .product-name {
    top: 916px;
    font-family: "Libre Baskerville", serif;
    font-size: 15.5px;
    letter-spacing: 0.3px;
  }
  .slogan {
    top: 963px;
    font-family: "Libre Baskerville", serif;
    font-weight: 700;
    font-size: 10px;
  }
  .organic {
    top: 990px;
    font-family: "Comfortaa", sans-serif;
    font-size: 18px;
    color: var(--organic);
  }
  .volume {
    top: 1034px;
    font-family: "Arimo", sans-serif;
    font-size: 13px;
    letter-spacing: 0.5px;
  }
</style>
</head>
<body>
<main class="canvas">
  <svg class="label-shape" width="716" height="1200" viewBox="0 0 716 1200" aria-hidden="true">
    <path class="label-drop" fill="var(--label)"
      d="M403 648
         C 380 680, 330 700, 285 740
         C 235 785, 222 840, 222 895
         C 222 995, 305 1075, 403 1075
         C 501 1075, 584 995, 584 895
         C 584 840, 571 785, 521 740
         C 476 700, 426 680, 403 648 Z"/>
    <path class="label-band" fill="var(--label)"
      d="M194 848 L612 848 L615 920 L191 920 Z"/>
    <line class="rule rule-top" x1="262" y1="910" x2="544" y2="910" stroke="var(--ink)" stroke-width="1.5"/>
    <line class="rule rule-bottom" x1="262" y1="939" x2="544" y2="939" stroke="var(--ink)" stroke-width="1.5"/>
    <path class="flourish flourish-left" fill="none" stroke="var(--ink)" stroke-width="1.5"
      d="M266 1001 C 285 997, 300 1004, 318 999 C 328 997, 338 1000, 348 999"/>
    <path class="flourish flourish-right" fill="none" stroke="var(--ink)" stroke-width="1.5"
      d="M458 999 C 470 1000, 480 997, 492 999 C 510 1003, 525 996, 540 1000"/>
  </svg>

  <div class="label-copy">
    <p class="label-text brand-name">MAPLE DEW GALA</p>
    <div class="product-art" role="img" aria-label="Illustration of a halved coconut with leaves"></div>
    <p class="label-text product-name">PURE COCONUT OIL</p>
    <p class="label-text slogan">HYDRATE YOUR SKIN AND HAIR</p>
    <p class="label-text organic">ORGANIC</p>
    <p class="label-text volume">236 ML</p>
  </div>
</main>
</body>
</html>
```